Web Developer Needs a Business Card Design

I need a personal business card design that represents me as a web developer for potential employers. I would like the background to be a dark color on the front for contrast with my logo and name. The back will have all my information along with a smaller version of the logo. I want something with a modern look and feel, not too conservative. This will be used for potential employers and freelance work.

Industry/Entity Type

Business

Contact Information for Business Card

Front should have my logo and name. The back should have all my personal information which would include: name: Tom Varulek, phone: 570-614-3098, email: tomvarulek@quillbox.net, website url: www.tomvarulek.net, logo, web developer.

Font styles to use
Sans Serif

Requirements
Must have
• Must include my logo. The color palette base color will be the logo color.

```html
<!DOCTYPE html>
<html lang="en">
<head>
<meta charset="utf-8">
<title>Tom Varulek — Business Card</title>
<link rel="stylesheet" href="https://fonts.googleapis.com/css2?family=Open+Sans:wght@300;400;600;700&display=swap">
<style>
  :root {
    --teal: #72d0bb;
    --ink: #0b0b0c;
    --paper: #ffffff;
    --stage: #e9e7e3;
    --grey-text: #2a2a2a;
  }
  * { margin: 0; padding: 0; box-sizing: border-box; }
  html, body {
    width: 1200px; height: 913px; overflow: hidden;
    background: var(--stage);
    font-family: "Open Sans", Arial, sans-serif;
  }
  .canvas { position: relative; width: 1200px; height: 913px; }

  .card {
    position: absolute; width: 560px; height: 320px;
    border-radius: 16px; overflow: hidden;
    box-shadow: 0 10px 28px rgba(0,0,0,.18);
  }
  .card-front { left: 70px; top: 90px; background: var(--ink); }
  .card-back { left: 570px; top: 500px; background: var(--paper); }

  .card-art { position: absolute; inset: 0; width: 100%; height: 100%; }

  .identity { position: absolute; left: 40px; top: 66px; line-height: 1.15; }
  .identity-name { color: var(--paper); font-weight: 700; font-size: 22px; letter-spacing: .5px; }
  .identity-role { color: var(--teal); font-weight: 600; font-size: 14px; letter-spacing: 1px; }

  .contacts { position: absolute; left: 118px; top: 178px; list-style: none; }
  .contacts li {
    display: flex; align-items: center; gap: 8px;
    color: var(--paper); font-size: 13.5px; line-height: 21px;
  }
  .contacts svg { width: 12px; height: 12px; flex: none; }

  .mark {
    position: absolute; display: flex; align-items: center; gap: 10px;
    color: var(--teal); font-weight: 600;
  }
  .card-front .mark {
    right: 26px; top: 50px; padding: 8px 10px;
    background: var(--ink); font-size: 30px;
  }
  .mark-dot { border-radius: 50%; background: var(--teal); flex: none; }
  .card-front .mark-dot { width: 26px; height: 26px; }

  .card-back .mark {
    left: 50%; top: 62px; transform: translateX(-50%); font-size: 28px;
  }
  .card-back .mark-dot { width: 24px; height: 24px; }

  .back-name {
    position: absolute; left: 0; right: 0; top: 150px; text-align: center;
    color: var(--grey-text); font-weight: 300; font-size: 36px; letter-spacing: 1.5px;
  }
  .back-role {
    position: absolute; left: 0; right: 0; top: 205px; text-align: center;
    color: var(--grey-text); font-weight: 400; font-size: 16px;
  }
</style>
</head>
<body>
<main class="canvas">

  <section class="card card-front" aria-label="Business card, dark side">
    <svg class="card-art" viewBox="0 0 560 320" aria-hidden="true">
      <line x1="0" y1="200" x2="560" y2="40" stroke="#ffffff" stroke-width="1.5"/>
      <path d="M0,268 C200,262 420,222 560,166 L560,190 C420,242 200,282 0,286 Z" fill="#ffffff"/>
      <path d="M0,286 C200,282 420,242 560,190 L560,320 L0,320 Z" fill="#72d0bb"/>
    </svg>

    <div class="identity">
      <div class="identity-name">TOM VARULEK</div>
      <div class="identity-role">WEB DEVELOPER</div>
    </div>

    <div class="mark"><span class="mark-dot"></span>Varulek</div>

    <ul class="contacts">
      <li>
        <svg viewBox="0 0 24 24" aria-hidden="true"><path fill="#72d0bb" d="M6.6 10.8a15 15 0 0 0 6.6 6.6l2.2-2.2c.3-.3.7-.4 1-.2 1.1.4 2.3.6 3.6.6.6 0 1 .4 1 1V20c0 .6-.4 1-1 1A17 17 0 0 1 3 4c0-.6.4-1 1-1h3.5c.6 0 1 .4 1 1 0 1.3.2 2.5.6 3.6.1.3 0 .7-.2 1z"/></svg>
        570-614-3098
      </li>
      <li>
        <svg viewBox="0 0 24 24" aria-hidden="true"><rect x="2" y="5" width="20" height="14" rx="2" fill="none" stroke="#72d0bb" stroke-width="2"/><path d="M3 6l9 7 9-7" fill="none" stroke="#72d0bb" stroke-width="2"/></svg>
        tomvarulek@quillbox.net
      </li>
      <li>
        <svg viewBox="0 0 24 24" aria-hidden="true"><circle cx="12" cy="12" r="9" fill="none" stroke="#72d0bb" stroke-width="2"/><path d="M3 12h18M12 3c3 3 3 15 0 18M12 3c-3 3-3 15 0 18" fill="none" stroke="#72d0bb" stroke-width="1.6"/></svg>
        www.tomvarulek.net
      </li>
    </ul>
  </section>

  <section class="card card-back" aria-label="Business card, white side">
    <div class="mark"><span class="mark-dot"></span>Varulek</div>
    <div class="back-name">TOM VARULEK</div>
    <div class="back-role">Front-End Developer</div>
  </section>

</main>
</body>
</html>
```